Amber Meadow Business Card and Logo

Nutrition and Wellness Store Front. I sell supplements, herbs, tinctures, Loose Leaf Teas, natural snacks and drinks including gluten free. classes: Fitness; health and wellness; community health and wellness hub. It is a "shabby chic" store front. It is white and my accent color is turqouise I will be adding some jewelry, stones and rocks and jewelery. I am a Certified Herbalist and Certified Nutrition and Wellness Consultant, a Reiki Practitioner and Kavolo instructor.

Target Market(s)

health and wellness seekers, fitness, baby boomer

Industry/Entity Type

Business

Contact Information for Business Card

Amber Meadow Nutrition and Wellness
Delia Marchetti Certified Herbalist , Certified Nutrition and Wellness Consultant, Reiki Practitioner, Kavolo Instructor

Font styles to use
Serif

Colors
33a6d7
3176b5
33b8a4

Requirements
Must have
• A picture that represents two mountain peaks with a floral accent.

```html
<!DOCTYPE html>
<html lang="en">
<head>
<meta charset="utf-8">
<title>Amber Meadow Nutrition and Wellness – Business Card</title>
<link href="https://fonts.googleapis.com/css2?family=Pinyon+Script&display=swap" rel="stylesheet">
<style>
  :root {
    --plum: #a5248d;
    --teal: #01a9a1;
    --ink: #111111;
    --white: #ffffff;
    --haze: rgba(225, 225, 225, 0.85);
    --script: "Pinyon Script", cursive;
  }
  html, body {
    margin: 0;
    padding: 0;
    width: 1200px;
    height: 702px;
    overflow: hidden;
    background: var(--plum);
  }
  .card {
    position: relative;
    width: 1200px;
    height: 702px;
    background: var(--plum);
    font-family: var(--script);
  }
  .card__panel {
    position: absolute;
    left: 46px;
    top: 39px;
    width: 1107px;
    height: 624px;
    background: var(--teal);
  }
  .card__dots {
    position: absolute;
    inset: 0;
  }
  .line {
    position: absolute;
    left: 46px;
    width: 1107px;
    margin: 0;
    text-align: center;
    white-space: nowrap;
    line-height: 1;
    font-weight: 400;
  }
  .credentials {
    color: var(--ink);
    font-size: 44px;
    -webkit-text-stroke: 0.6px var(--ink);
  }
  .credentials--first { top: 49px; }
  .credentials--second { top: 112px; font-size: 45px; }
  .business-name {
    color: var(--ink);
    -webkit-text-stroke: 1.2px var(--ink);
    text-shadow: 6px 8px 6px var(--haze), -4px 6px 6px var(--haze);
  }
  .business-name--first { top: 181px; font-size: 118px; }
  .business-name--second { top: 343px; font-size: 124px; }
  .offerings {
    color: var(--white);
    -webkit-text-stroke: 0.6px var(--white);
  }
  .offerings--products { top: 482px; font-size: 56px; }
  .offerings--snacks { top: 573px; font-size: 58px; }
  .offerings--classes { top: 626px; font-size: 36px; -webkit-text-stroke: 0.3px var(--white); }
  .bullet {
    display: inline-block;
    width: 15px;
    height: 15px;
    margin: 0 16px;
    border-radius: 50%;
    background: var(--plum);
    vertical-align: middle;
  }
  .offerings--classes .bullet {
    width: 13px;
    height: 13px;
    margin: 0 4px;
  }
</style>
</head>
<body>
<main class="card">
  <div class="card__panel"></div>

  <svg class="card__dots" width="1200" height="702" viewBox="0 0 1200 702" aria-hidden="true">
    <g fill="var(--plum)">
      <circle cx="46" cy="160" r="34"/>
      <circle cx="46" cy="238" r="34"/>
      <circle cx="46" cy="321" r="34"/>
      <circle cx="46" cy="398" r="34"/>
      <circle cx="122" cy="205" r="34"/>
      <circle cx="122" cy="288" r="34"/>
      <circle cx="194" cy="243" r="34"/>

      <circle cx="1154" cy="160" r="34"/>
      <circle cx="1154" cy="238" r="34"/>
      <circle cx="1154" cy="321" r="34"/>
      <circle cx="1154" cy="398" r="34"/>
      <circle cx="1078" cy="205" r="34"/>
      <circle cx="1078" cy="288" r="34"/>
      <circle cx="1006" cy="243" r="34"/>
    </g>
  </svg>

  <p class="line credentials credentials--first">Certified Herbalist and Certified Nutrition and Wellness Consultant</p>
  <p class="line credentials credentials--second">Reiki Practitioner and Kavolo Instructor</p>

  <h1 class="line business-name business-name--first">Amber Meadow</h1>
  <p class="line business-name business-name--second">Nutrition and Wellness</p>

  <p class="line offerings offerings--products">Supplements<span class="bullet"></span>Herbs<span class="bullet"></span>Tinctures<span class="bullet"></span>Loose Leaf Teas</p>
  <p class="line offerings offerings--snacks">Natural Snacks And Drinks Including Gluten Free</p>
  <p class="line offerings offerings--classes">Health and Wellness Classes: Kavolo Gold and Yoga<span class="bullet"></span>Stones and Rocks Jewelery</p>
</main>
</body>
</html>
```